Plakat für Tanzschule
Zielgruppe
Wir sind eine Tanzschule
Hallo,
ich benötige ein professionelles Design für ein Schild im Format 2 Meter breit × 1 Meter hoch (Querformat), das von einem stark frequentierten Parkplatz aus gut sichtbar ist.
✅ Ziel:
Gestaltung eines aufmerksamkeitsstarken, eleganten und energiegeladenen Werbeschilds
Das Schild soll sofort zeigen, worum es geht (Tanzstile) und zum kostenlosen Schnuppern motivieren
Die Gestaltung soll hochwertig und grafisch modern wirken
Bild / Hintergrund:
Ich habe einen ersten Design-Vorschlag hochgeladen (Screenshot)
⚠️ Ursprünglich hatte ich vor, ein bereits ausgeschnittenes und bearbeitetes Bild zu liefern (z. B. Unreinheiten und Störungen im Bild zu glätten oder zu entfernt und Zähne etwas weißer). Das kann ich jetzt leider doch nicht nachreichen. Daher müsste doch die Bearbeitung des Bildes mit übernommen werden.
✏️ Textinhalte (hierarchisch sortiert):
TANZSCHULE
Salsa · Bachata · Kizomba · Zouk
Jetzt Gratis Schnuppern!
Ritmo del Faro (Markenname)
www.ritmo-del-faro.de
???? Wichtig:
Die wichtigsten Inhalte (Tanzarten & CTA) müssen sofort erfassbar sein
Design bitte auf Fernwirkung, klare Lesbarkeit und modernes visuelles Layout ausrichten
Text in sinnvollen Größenabstufungen und mit sauberer visueller Hierarchie
Unsere eigentliche Hauptfarbe ist #ad194f, bis jetzt habe ich aber noch keine schöne Möglichkeit gefunden, in das aktuelle Design einzuarbeiten.
????️ Endformat & Übergabe:
Bitte das fertige Layout als .afdesign Datei (Affinity Designer) liefern
Optional PSD, EPS

```html
<!DOCTYPE html>
<html lang="de">
<head>
<meta charset="utf-8">
<title>Tanzschule Ritmo del Faro – Schild</title>
<link rel="stylesheet" href="https://fonts.googleapis.com/css2?family=Krona+One&family=Poppins:wght@400;500;800&display=swap">
<style>
  :root {
    --stage: #1b1b1b;
    --forest: #2e4c36;
    --forest-light: #3b6446;
    --olive: #5e7444;
    --olive-dark: #4d6238;
    --hair: #c9a46c;
    --skin: #d9a488;
    --top-white: #e9e6e4;
    --shirt: #5f806a;
    --white: #ffffff;
    --brand: #ad194f;
    --pill: #f7f4f4;
    --grey-light: #a9b0b5;
    --grey-blue: #7c8f99;
    --ink: #1e1e1e;
    --ink-soft: #4a4a4a;
  }
  * { margin: 0; padding: 0; box-sizing: border-box; }
  html, body {
    width: 1200px; height: 800px; overflow: hidden;
    background: var(--stage);
  }
  .sign {
    position: absolute; left: 0; top: 100px;
    width: 1200px; height: 600px;
    background: var(--forest);
    overflow: hidden;
  }
  .sign__photo {
    position: absolute; left: 500px; top: 0;
    width: 700px; height: 600px;
    background:
      radial-gradient(ellipse 14% 22% at 33% 28%, rgba(201,164,108,0.95) 0%, rgba(201,164,108,0) 100%),
      radial-gradient(ellipse 9% 12% at 61% 12%, rgba(217,164,136,0.7) 0%, rgba(217,164,136,0) 100%),
      radial-gradient(ellipse 8% 11% at 86% 18%, rgba(217,164,136,0.8) 0%, rgba(217,164,136,0) 100%),
      radial-gradient(ellipse 14% 26% at 56% 70%, rgba(233,230,228,0.9) 0%, rgba(233,230,228,0) 100%),
      radial-gradient(ellipse 22% 45% at 84% 62%, rgba(95,128,106,0.95) 0%, rgba(95,128,106,0) 100%),
      radial-gradient(ellipse 40% 60% at 68% 40%, var(--olive) 0%, rgba(94,116,68,0) 75%),
      radial-gradient(ellipse 30% 40% at 20% 95%, var(--olive-dark) 0%, rgba(77,98,56,0) 80%),
      linear-gradient(90deg, var(--forest) 0%, var(--forest-light) 60%, var(--forest-light) 100%);
  }
  .sign__kicker {
    position: absolute; left: 55px; top: 106px;
    font-family: "Krona One", sans-serif;
    font-size: 30px; letter-spacing: 2px;
    color: var(--grey-light);
    line-height: 1;
  }
  .sign__styles {
    position: absolute; left: 0; top: 0;
    width: 700px; height: 600px;
  }
  .style-name {
    font-family: "Krona One", sans-serif;
    font-size: 70px;
    fill: var(--white);
    text-transform: uppercase;
  }
  .style-dot { fill: var(--brand); }
  .brand-pill {
    position: absolute; left: 421px; top: 385px;
    width: 310px; height: 82px;
    background: var(--pill);
    border-radius: 41px 0 0 41px;
    display: flex; align-items: center; gap: 14px;
    padding-left: 28px;
  }
  .brand-pill__text { display: flex; flex-direction: column; gap: 2px; }
  .brand-pill__name {
    font-family: "Poppins", sans-serif;
    font-weight: 500; font-size: 26px; line-height: 1.05;
    color: var(--ink);
    white-space: nowrap;
  }
  .brand-pill__url {
    font-family: "Poppins", sans-serif;
    font-weight: 400; font-size: 12px; line-height: 1.2;
    color: var(--ink-soft);
    white-space: nowrap;
  }
  .brand-pill__dot {
    width: 40px; height: 40px; border-radius: 50%;
    background: var(--brand);
    flex: none;
  }
  .sign__cta {
    position: absolute; left: 55px; top: 482px;
    font-family: "Poppins", sans-serif;
    font-weight: 800; font-size: 46px;
    letter-spacing: -0.5px; line-height: 1;
    color: var(--grey-light);
    white-space: nowrap;
  }
  .sign__cta-accent { color: var(--grey-blue); }
</style>
</head>
<body>
  <main class="sign">
    <div class="sign__photo" role="img" aria-label="Foto eines lachenden Tanzpaares: Frau mit wehendem blondem Haar im weißen Top, Mann im grünen T-Shirt, vor olivgrünen Schattenformen"></div>

    <p class="sign__kicker">TANZSCHULE</p>

    <svg class="sign__styles" viewBox="0 0 700 600" aria-label="Salsa, Bachata, Kizomba, Zouk">
      <circle class="style-dot" cx="91" cy="188" r="27"/>
      <text class="style-name" x="139" y="213" textLength="322" lengthAdjust="spacingAndGlyphs">Salsa</text>

      <text class="style-name" x="29" y="289" textLength="475" lengthAdjust="spacingAndGlyphs">Bachata</text>
      <circle class="style-dot" cx="552" cy="262" r="27"/>

      <circle class="style-dot" cx="91" cy="337" r="27"/>
      <text class="style-name" x="139" y="363" textLength="472" lengthAdjust="spacingAndGlyphs">Kizomba</text>

      <text class="style-name" x="27" y="437" textLength="281" lengthAdjust="spacingAndGlyphs">Zouk</text>
      <circle class="style-dot" cx="366" cy="412" r="27"/>
    </svg>

    <div class="brand-pill">
      <div class="brand-pill__text">
        <span class="brand-pill__name">Ritmo del Faro</span>
        <span class="brand-pill__url">www.ritmo-del-faro.de</span>
      </div>
      <span class="brand-pill__dot"></span>
    </div>

    <p class="sign__cta">Jetzt Gratis <span class="sign__cta-accent">Schnuppern!</span></p>
  </main>
</body>
</html>
```